Our companies name is The Gilded Ladle and we specialize in craft cupcakes, what I mean by that is that we bake our cupcakes with craft beer and other alcoholic drinks. We are trying to focus on being elegant but at the same time unpretentious. Since we are incorporating beer in our cupcakes we want the business card to have our logo in the front and our information in the back.

Once we select the best design we will provide the contact information to be added. Thank you.

Industry/Entity Type

Business

Font styles to use
Decorative
Script

Requirements
Must have
• Round corners
Should not have
• Square corners

```html
<!DOCTYPE html>
<html lang="en">
<head>
<meta charset="utf-8">
<title>The Gilded Ladle – Business Card</title>
<link rel="stylesheet" href="https://fonts.googleapis.com/css2?family=Rye&family=Arimo:wght@400&display=swap">
<style>
  :root {
    --canvas: #e9e6e1;
    --card: #070808;
    --teal: #86cfc6;
    --red: #e8262f;
    --heading: "Rye", serif;
    --body: "Arimo", sans-serif;
  }
  * { box-sizing: border-box; margin: 0; padding: 0; }
  html, body { width: 1200px; height: 848px; overflow: hidden; background: var(--canvas); }
  .sheet {
    width: 1200px; height: 848px;
    display: flex; flex-direction: column; align-items: center; justify-content: center; gap: 24px;
  }
  .card {
    position: relative; width: 680px; height: 388px;
    background: var(--card); border-radius: 18px; overflow: hidden;
    box-shadow: 0 6px 18px rgba(0,0,0,.18);
  }
  /* info side */
  .card-info .brand-panel {
    position: absolute; left: 0; top: 0; width: 300px; height: 308px;
    display: flex; flex-direction: column; align-items: center; justify-content: center; gap: 14px;
  }
  .brand-dot { width: 18px; height: 18px; border-radius: 50%; background: var(--red); }
  .brand-name {
    font-family: var(--heading); color: var(--teal); font-size: 30px; line-height: 1.15; text-align: center;
  }
  .divider { position: absolute; left: 300px; top: 20px; width: 1px; height: 288px; background: var(--teal); opacity: .7; }
  .contact-panel { position: absolute; left: 336px; top: 62px; right: 24px; }
  .employee-name { font-family: var(--heading); color: var(--teal); font-size: 25px; letter-spacing: .5px; }
  .employee-role { font-family: var(--body); color: var(--teal); font-size: 15px; margin-top: 6px; margin-left: 14px; }
  .contact-list { list-style: none; margin-top: 42px; margin-left: 56px; }
  .contact-list li {
    display: flex; align-items: center; gap: 18px;
    font-family: var(--body); color: var(--teal); font-size: 17px; height: 30px;
  }
  .contact-list svg { width: 18px; height: 18px; flex: none; }
  .address-band {
    position: absolute; left: 0; right: 0; bottom: 0; height: 80px; background: var(--teal);
    display: flex; align-items: center; padding-left: 150px; gap: 40px;
    font-family: var(--body); font-size: 22px; color: var(--card);
  }
  .address-band svg { width: 20px; height: 26px; }
  /* logo side */
  .card-logo { display: flex; flex-direction: column; align-items: center; justify-content: center; gap: 34px; }
  .card-logo .brand-name { font-size: 40px; }
  .web-line { display: flex; align-items: center; gap: 18px; }
  .web-line .rule { width: 150px; height: 1.5px; background: var(--red); }
  .web-address { font-family: var(--heading); color: var(--teal); font-size: 17px; letter-spacing: 1px; }
</style>
</head>
<body>
<main class="sheet">
  <section class="card card-info">
    <div class="brand-panel">
      <span class="brand-dot"></span>
      <h1 class="brand-name">The Gilded<br>Ladle</h1>
    </div>
    <div class="divider"></div>
    <div class="contact-panel">
      <h2 class="employee-name">EMPLOYEE NAME</h2>
      <p class="employee-role">Managing Director</p>
      <ul class="contact-list">
        <li>
          <svg viewBox="0 0 20 20" aria-hidden="true"><path fill="#e8262f" d="M3 6c0-2 3-3 7-3s7 1 7 3v2h-4V6.5c-1-.4-5-.4-6 0V8H3zM5 9h10l2 8H3z"/></svg>
          0012 3456 789
        </li>
        <li>
          <svg viewBox="0 0 20 20" aria-hidden="true"><rect x="1" y="4" width="18" height="12" fill="#e8262f"/><path d="M1 4l9 7 9-7" fill="none" stroke="#070808" stroke-width="1.5"/></svg>
          info@gildedladle.com
        </li>
        <li>
          <svg viewBox="0 0 20 20" aria-hidden="true"><circle cx="10" cy="10" r="8" fill="#e8262f"/><path d="M2 10h16M10 2c-3 3-3 13 0 16M10 2c3 3 3 13 0 16" fill="none" stroke="#070808" stroke-width="1.2"/></svg>
          www.gildedladle.com
        </li>
      </ul>
    </div>
    <div class="address-band">
      <svg viewBox="0 0 20 26" aria-hidden="true"><path d="M10 1a8 8 0 0 0-8 8c0 6 8 15 8 15s8-9 8-15a8 8 0 0 0-8-8z" fill="none" stroke="#070808" stroke-width="2.2"/><circle cx="10" cy="9" r="3" fill="#070808"/></svg>
      <span>Address your Inc 00 2nd, Ave Larkfield, NJ xxxxx</span>
    </div>
  </section>

  <section class="card card-logo">
    <h1 class="brand-name">The Gilded Ladle</h1>
    <div class="web-line">
      <span class="rule"></span>
      <span class="web-address">WWW.GILDEDLADLE.COM</span>
      <span class="rule"></span>
    </div>
  </section>
</main>
</body>
</html>
```